Web design project for exciting Australian start-up

Background
We are looking for a creative and talented web design artist to work alongside our market leading web developer.
• You will be required to create a modern and clean design theme for our website, incorporating selected rustic colour scheme elements for our exciting Australian start-up to operate within the coffee industry.
reoccurring work to be expected to flow to the successful designer.
Requirements
• c. 5 - 10 page website
• Landing page
• Log in/ out
• 404 template
• Typography is emphasised
• Please use either a) typemarrow.com, b) free web fonts, c) brindle fonts
• All design elements in vector format
• Preferably with icons for each header title(i.e. about us, how it works etc) but designer have free reign over how the site looks, so might not be applicable
• All pages to be responsive
• Down to eSlab resolution

High level visual design brief attached - additional pages to be worked from base design.

Design inspiration
• We would like to use design elements from the following sources:
http://www.zandrix.com/halcyon/ (Functionality)
Colour scheme refer to logo and complementary style guide

```html
<!DOCTYPE html>
<html lang="en">
<head>
<meta charset="utf-8">
<title>Bean Commons — Australia's First Online Coffee Marketplace</title>
<link rel="stylesheet" href="https://fonts.googleapis.com/css2?family=Open+Sans:wght@400;600&family=Zilla+Slab:wght@300&display=swap">
<style>
  :root {
    --cream: #f1f0e4;
    --charcoal: #2b2b2b;
    --ink: #1c1c1c;
    --muted: #6f6f6f;
    --red: #d83a3a;
    --orange: #f79a4c;
    --register: #ef4a55;
    --field: #f4f4f1;
    --field-line: #cfcfca;
    --submit: #6f6f6f;
    --white: #ffffff;
    --friendlane: #3b5b99;
    --chirrup: #2ab4e6;
    --netweave: #1a78b4;
    --viewreel: #b8231e;
  }
  * { box-sizing: border-box; margin: 0; padding: 0; }
  html, body { width: 1200px; height: 963px; overflow: hidden; }
  body {
    position: relative;
    background: var(--cream);
    font-family: "Open Sans", Arial, sans-serif;
    color: var(--ink);
  }

  /* Header */
  .site-header { position: absolute; left: 0; top: 0; width: 1200px; height: 140px; }
  .brand {
    position: absolute; left: 99px; top: 50px;
    display: flex; align-items: center; gap: 12px;
    font-weight: 600; font-size: 30px; letter-spacing: 1px;
    color: var(--ink); text-transform: uppercase; white-space: nowrap;
  }
  .brand-dot { width: 34px; height: 34px; border-radius: 50%; background: var(--ink); }
  .account-nav { position: absolute; top: 54px; left: 943px; display: flex; gap: 8px; }
  .btn-account {
    display: block; height: 27px; line-height: 27px; padding: 0;
    border-radius: 3px; font-size: 13px; font-weight: 600; text-transform: uppercase;
    text-decoration: none; text-align: center; white-space: nowrap;
  }
  .btn-login { background: var(--orange); color: var(--ink); width: 66px; }
  .btn-register { background: var(--register); color: var(--white); width: 83px; }

  /* Hero */
  .hero { position: absolute; left: 0; top: 140px; width: 1200px; height: 513px; overflow: hidden; }
  .hero-photo {
    position: absolute; inset: 0;
    background: linear-gradient(180deg, #9a7252 0%, #b98d66 50%, #c9a27c 100%);
  }
  .hero-title {
    position: absolute; left: 100px; top: 82px;
    font-family: "Zilla Slab", Georgia, serif; font-weight: 300;
    font-size: 37px; line-height: 48px; color: var(--white); text-transform: uppercase;
    letter-spacing: 0.3px; white-space: nowrap; text-shadow: 0 1px 3px rgba(0,0,0,0.3);
  }
  .btn-video {
    position: absolute; left: 101px; top: 237px; width: 203px; height: 47px;
    background: var(--white); border-radius: 2px;
    display: flex; align-items: center; justify-content: center; gap: 10px;
    font-size: 20px; font-weight: 600; color: #555; text-transform: uppercase;
    text-decoration: none; white-space: nowrap;
  }
  .slider-next { position: absolute; left: 1057px; top: 234px; width: 42px; height: 42px; }

  /* Footer links */
  .footer-main { position: absolute; left: 0; top: 653px; width: 1200px; height: 236px; }
  .footer-col { position: absolute; top: 36px; }
  .footer-col h2 { font-size: 16px; font-weight: 400; color: var(--red); margin-bottom: 4px; white-space: nowrap; }
  .footer-col ul { list-style: none; padding-left: 2px; }
  .footer-col li { font-size: 12.5px; line-height: 23px; color: #555; white-space: nowrap; }
  .col-info { left: 143px; }
  .col-about { left: 342px; }
  .col-signup { left: 551px; width: 230px; }
  .col-connect { left: 860px; }
  .signup-form { padding-left: 2px; padding-top: 3px; }
  .field {
    display: block; width: 227px; height: 29px; margin-bottom: 13px;
    background: var(--field); border: 1px solid var(--field-line);
    font-family: inherit; font-size: 11.5px; color: var(--ink); padding-left: 16px;
  }
  .field::placeholder { color: var(--ink); }
  .btn-submit {
    display: block; margin-left: 157px; width: 70px; height: 30px;
    background: var(--submit); color: var(--white); border: 0; border-radius: 2px;
    font-family: inherit; font-size: 13px; font-weight: 600; text-transform: uppercase;
    box-shadow: 0 2px 0 #4e4e4e;
  }
  .social-list { list-style: none; padding-top: 3px; }
  .social-item { display: flex; align-items: center; height: 27px; margin-bottom: 13px; font-size: 12px; color: var(--muted); white-space: nowrap; }
  .social-mark { width: 27px; height: 27px; border-radius: 2px; margin-right: 10px; flex: none; }
  .social-item strong { font-weight: 400; font-size: 15px; margin-left: 6px; }
  .net-friendlane .social-mark { background: var(--friendlane); } .net-friendlane strong { color: var(--friendlane); }
  .net-chirrup .social-mark { background: var(--chirrup); } .net-chirrup strong { color: var(--chirrup); }
  .net-netweave .social-mark { background: var(--netweave); } .net-netweave strong { color: var(--netweave); }
  .net-viewreel .social-mark { background: var(--viewreel); } .net-viewreel strong { color: var(--viewreel); }

  /* Bottom bar */
  .site-bar {
    position: absolute; left: 0; top: 889px; width: 1200px; height: 74px;
    background: var(--charcoal); color: #b9b9b9; font-size: 13.5px;
    display: flex; align-items: center; justify-content: center; white-space: nowrap;
  }
</style>
</head>
<body>
  <header class="site-header">
    <div class="brand"><span>Bean</span><span class="brand-dot"></span><span>Commons</span></div>
    <nav class="account-nav">
      <a class="btn-account btn-login" href="#">Log in</a>
      <a class="btn-account btn-register" href="#">Register</a>
    </nav>
  </header>

  <section class="hero">
    <div class="hero-photo" role="img" aria-label="Photo of a steaming white coffee cup on a saucer with roasted coffee beans on a hessian background"></div>
    <h1 class="hero-title">Australia's first<br>online coffee<br>marketplace</h1>
    <a class="btn-video" href="#">Watch video
      <svg width="19" height="19" viewBox="0 0 19 19" aria-hidden="true"><circle cx="9.5" cy="9.5" r="9.5" fill="#555"/><path d="M8 5.5l4 4-4 4" fill="none" stroke="#fff" stroke-width="2"/></svg>
    </a>
    <svg class="slider-next" viewBox="0 0 42 42" aria-label="Next slide"><circle cx="21" cy="21" r="21" fill="#d9cfc4" fill-opacity="0.85"/><path d="M18 14l7 7-7 7" fill="none" stroke="#8a7c70" stroke-width="1.6"/></svg>
  </section>

  <footer class="footer-main">
    <div class="footer-col col-info">
      <h2>Helpful info</h2>
      <ul><li>About us</li><li>Media enquiries</li><li>Terms &amp; conditions</li><li>Privacy policy</li></ul>
    </div>
    <div class="footer-col col-about">
      <h2>Who we are</h2>
      <ul><li>How it works</li><li>FAQ</li><li>Contact us</li></ul>
    </div>
    <div class="footer-col col-signup">
      <h2>Email Signup</h2>
      <form class="signup-form">
        <input class="field" type="text" placeholder="Name">
        <input class="field" type="email" placeholder="Email ID">
        <button class="btn-submit" type="button">Submit</button>
      </form>
    </div>
    <div class="footer-col col-connect">
      <h2>Connect with us</h2>
      <ul class="social-list">
        <li class="social-item net-friendlane"><span class="social-mark"></span>Join with us on <strong>Friendlane</strong></li>
        <li class="social-item net-chirrup"><span class="social-mark"></span>Follow us on <strong>Chirrup</strong></li>
        <li class="social-item net-netweave"><span class="social-mark"></span>Share on <strong>Netweave</strong></li>
        <li class="social-item net-viewreel"><span class="social-mark"></span>Watch on <strong>Viewreel</strong></li>
      </ul>
    </div>
  </footer>

  <div class="site-bar">Copyright © 2014 Bean Commons. &nbsp; All rights reserved.</div>
</body>
</html>
```